a business advisory consulting website

I need a website 3-5 pages to sell my professional services in IT and Project management Consulting. My company name is Crestline Advisory Consulting. I want it to be device friendly and easy to navigate for the busy executive however intriguing enough.
I have attached some info I drafted on About the company and personal Bio. Also there is a website that I really like that I have attached the initial site pdf and websites that I like are here: https://tollmeradvisors.example, https://quarvelanalytics.example, https://www.dorvikstudylearning.example as examples. Thanks
Updates

Hi Designers, I have uploaded the logo in 3D .png format, to assist in the web design.

Target Market(s)

B2B, governments, IT companies, Project Management companies and Consulting firms, small medium enterprises to large corporate enterprises.

Industry/Entity Type

It Professional

Coding

Coded - Design and coding required

Number of Pages Required

5+ page

Font styles to use
Sans Serif

Requirements
Must have
• Home, About company, the team, what we do and contact us
Nice to have
• Blog
Should not have
• pop ups, flash

```html
<!DOCTYPE html>
<html lang="en">
<head>
<meta charset="utf-8">
<title>Crestline Advisory Consulting</title>
<link href="https://fonts.googleapis.com/css2?family=Rokkitt:wght@400;600;700;800&family=Roboto:wght@300;400;500&display=swap" rel="stylesheet">
<style>
:root{
  --red:#d90b1f;
  --navy:#1c1f36;
  --navy-soft:#2c3560;
  --ink:#111;
  --grey:#555;
  --light:#efefef;
  --white:#fff;
}
*{box-sizing:border-box;margin:0;padding:0}
html,body{width:1200px;height:3141px;overflow:hidden;background:var(--white);font-family:"Roboto",Arial,sans-serif}
.page{position:relative;width:1200px;height:3141px;overflow:hidden}
.abs{position:absolute}
.slab{font-family:"Rokkitt",Georgia,serif}

/* header */
.site-header{left:0;top:0;width:1200px;height:107px;background:var(--white);z-index:5}
.brand{display:flex;align-items:center;gap:12px;color:var(--navy);font-family:"Rokkitt",Georgia,serif;font-weight:700;font-size:27px;line-height:26px;letter-spacing:.5px}
.brand-mark{width:34px;height:34px;background:var(--red)}
.site-header .brand{left:64px;top:24px}
.main-nav{left:370px;top:36px;display:flex;gap:54px;font-size:16.5px;color:var(--ink);align-items:center}
.main-nav .active{font-weight:500}
.nav-cta{left:960px;top:24px;width:172px;height:46px;border-radius:23px;background:var(--red);color:var(--white);font-size:16.5px;display:flex;align-items:center;justify-content:center;box-shadow:0 3px 8px rgba(0,0,0,.2)}

/* hero */
.hero-photo{left:0;top:107px;width:1200px;height:663px;clip-path:polygon(0 0,100% 0,100% 513px,50% 663px,0 513px);background:linear-gradient(120deg,#3b3b3b 0%,#6d6a62 35%,#8f8c85 55%,#4d4f52 80%,#2c2c2c 100%)}
.hero-title{left:0;width:1200px;text-align:center;color:var(--white);text-shadow:0 2px 6px rgba(0,0,0,.35)}
.hero-line1{top:304px;font-size:52px;font-weight:400}
.hero-line2{top:362px;font-size:62px;font-weight:700}
.btn-red{background:var(--red);color:var(--white);border-radius:30px;display:flex;align-items:center;justify-content:center;font-family:"Rokkitt",Georgia,serif;font-weight:700;font-size:19px}
.hero-btn{left:482px;top:444px;width:216px;height:57px}
.chevron{top:358px}

/* about */
.section-title{left:0;width:1200px;text-align:center;font-family:"Rokkitt",Georgia,serif;font-weight:700;font-size:40px}
.about-title{top:854px;color:var(--ink)}
.about-title span{color:var(--red)}
.rule{height:3px;width:64px;background:var(--navy)}
.about-copy{left:160px;width:880px;text-align:center;color:var(--grey);font-size:17.5px;line-height:27px}
.about-copy p+p{margin-top:12px}
.btn-outline{left:515px;top:1113px;width:176px;height:47px;border:2px solid var(--red);border-radius:24px;color:var(--red);font-family:"Rokkitt",Georgia,serif;font-weight:700;font-size:17px;display:flex;align-items:center;justify-content:center}

/* services */
.services{left:0;top:1237px;width:1200px;height:593px;background:var(--red);clip-path:polygon(0 0,100% 0,100% 443px,50% 593px,0 443px);z-index:2}
.services-title{top:1304px;color:var(--white);z-index:3}
.service-card{top:1388px;width:316px;height:263px;background:var(--navy);color:var(--white);z-index:3;display:flex;flex-direction:column;align-items:center;padding-top:52px;text-align:center;font-family:"Rokkitt",Georgia,serif;font-size:23px;line-height:28px}
.service-card svg{margin-bottom:18px}
.service-card b{font-weight:800}

/* bio */
.bio-band{left:0;top:1680px;width:1200px;height:688px;background:var(--light)}
.bio-photo{left:0;top:1680px;width:650px;height:688px;background:linear-gradient(90deg,#3a3a3a 0%,#7a7a7a 40%,#bdbdbd 75%,var(--light) 100%)}
.bio-label{left:650px;top:1918px;font-size:28px;color:var(--ink);font-family:"Rokkitt",Georgia,serif;font-weight:600}
.bio-name{left:650px;top:1950px;font-size:34px;color:var(--ink);font-family:"Rokkitt",Georgia,serif;font-weight:700}
.bio-copy{left:651px;top:2024px;width:500px;color:var(--grey);font-size:16.5px;line-height:27px}
.bio-btn{left:649px;top:2234px;width:188px;height:51px}

/* contact */
.contact{left:0;top:2367px;width:1200px;height:616px;background:linear-gradient(180deg,#2b3461 0%,#343d6b 40%,#252c52 100%)}
.contact-title{top:2420px;color:var(--white);font-size:38px}
.info-item{left:145px;display:flex;gap:20px;color:var(--white);font-size:19px;line-height:28px}
.info-item .label{font-weight:300;color:#dde}
.info-item svg{flex:none;margin-top:10px}
.social{left:148px;top:2818px;display:flex;gap:38px}
.social span{width:18px;height:18px;border-radius:50%;background:var(--white);display:block}
.field{left:601px;width:435px;background:var(--white);border:1px solid #ddd;color:#333;font-size:15px;padding:18px 22px 0}
.submit{left:593px;top:2818px;width:174px;height:48px;font-size:18px}

/* footer */
.site-footer .brand{left:127px;top:3035px;font-size:30px;line-height:29px}
.footer-nav{left:419px;top:3030px;display:flex;gap:50px;font-size:15.5px;color:var(--ink)}
.copyright{left:419px;top:3068px;font-size:14.5px;color:#888}
</style>
</head>
<body>
<div class="page">

  <header class="site-header abs">
    <div class="brand abs"><span class="brand-mark"></span><span>CRESTLINE<br>ADVISORY</span></div>
    <nav class="main-nav abs">
      <span class="active">HOME</span><span>ABOUT COMPANY</span><span>THE TEAM</span><span>WHAT WE DO</span>
    </nav>
    <div class="nav-cta abs">CONTACT US</div>
  </header>

  <section class="hero">
    <div class="hero-photo abs" role="img" aria-label="Two business consultants reviewing charts on a tablet at a desk"></div>
    <h1 class="hero-title hero-line1 abs slab">WECOME TO</h1>
    <div class="hero-title hero-line2 abs slab">CRESTLINE ADVISORY</div>
    <div class="hero-btn btn-red abs">LEARN MORE</div>
    <svg class="chevron abs" style="left:56px" width="24" height="40" viewBox="0 0 24 40"><path d="M20 4 4 20l16 16" fill="none" stroke="#fff" stroke-width="5"/></svg>
    <svg class="chevron abs" style="left:1120px" width="24" height="40" viewBox="0 0 24 40"><path d="M4 4l16 16L4 36" fill="none" stroke="#fff" stroke-width="5"/></svg>
  </section>

  <section class="about">
    <h2 class="section-title about-title abs">ABOUT <span>CRESTLINE ADVISORY</span></h2>
    <div class="rule abs" style="left:561px;top:908px"></div>
    <div class="about-copy abs" style="top:932px">
      <p>We are a specialist operational excellence firm, delivering consulting and advisory services in six core capabilities, across all industries and all business lines to improve performance, efficiency, profitability, automation and scalability, for clients across Australia.</p>
      <p>We’re known for our pragmatism, in depth analysis, strategic insight and nurturing long-term client self-sufficiency. We approach business consulting differently, with a Genuine Client</p>
    </div>
    <div class="btn-outline abs">LEARN MORE</div>
  </section>

  <div class="bio-band abs"></div>
  <div class="bio-photo abs" role="img" aria-label="Black and white portrait of a consultant working at a desk with reports"></div>

  <section class="services abs"></section>
  <h2 class="section-title services-title abs">WHAT WE DO</h2>
  <div class="rule abs" style="left:586px;top:1354px;background:#fff;z-index:3;width:48px"></div>

  <div class="service-card abs" style="left:115px">
    <svg width="70" height="66" viewBox="0 0 70 66" fill="none" stroke="#fff" stroke-width="2"><rect x="4" y="4" width="34" height="26"/><path d="M10 12h22M10 18h22M10 24h14M21 30v10"/><circle cx="52" cy="14" r="7"/><path d="M42 62V34h20v28M44 34l8 10 8-10"/><circle cx="14" cy="52" r="6"/><circle cx="14" cy="52" r="2"/></svg>
    <span>STRATEGY<br><b>ANALYTICS</b></span>
  </div>
  <div class="service-card abs" style="left:442px">
    <svg width="70" height="70" viewBox="0 0 70 70" fill="none" stroke="#fff" stroke-width="2"><rect x="6" y="4" width="36" height="58"/><rect x="12" y="10" width="24" height="10"/><path d="M12 28h6M21 28h6M30 28h6M12 36h6M21 36h6M30 36h6"/><circle cx="28" cy="52" r="9"/><path d="M28 46v12M31 49h-4a2 2 0 0 0 0 4h2a2 2 0 0 1 0 4h-4"/><path d="M44 12h12v20M50 60l14-22-4-3-14 22z"/></svg>
    <span>FINANCE<br><b>ACCOUNTING</b></span>
  </div>
  <div class="service-card abs" style="left:770px">
    <svg width="70" height="70" viewBox="0 0 70 70" fill="none" stroke="#fff" stroke-width="2"><path d="M62 6c-16 0-28 8-36 22l14 14c14-8 22-20 22-36z"/><circle cx="46" cy="22" r="5"/><path d="M26 28l-12 2-6 8 12 2M40 42l-2 12-8 6-2-12M18 46l-10 10M22 52l-8 10M14 42l-8 8"/></svg>
    <span>ADVISE FOR<br><b>EARLY STAGE<br>STARTUPS</b></span>
  </div>

  <section class="bio">
    <div class="bio-label abs">BIO</div>
    <h2 class="bio-name abs">DANIEL OKWARA</h2>
    <div class="rule abs" style="left:651px;top:1995px"></div>
    <p class="bio-copy abs">Daniel Okwara is an IT professional with more than 20 years of experience turning business initiatives into technology solutions. His expertise has been identifying deficiencies and developing or facilitating the best solutions for an outcome that is satisfactory to all stakeholders involved.<br>Daniel improves business processes as older organizations restructure or migrate to newer technologies.</p>
    <div class="bio-btn btn-red abs">LEARN MORE</div>
  </section>

  <section class="contact abs" role="img" aria-label="Dark blue toned city skyline at dusk"></section>
  <h2 class="section-title contact-title abs">CONTACT US</h2>
  <div class="rule abs" style="left:574px;top:2474px;background:#fff"></div>

  <div class="info-item abs" style="top:2546px">
    <svg width="32" height="42" viewBox="0 0 32 42"><path d="M16 0C7 0 0 7 0 16c0 11 16 26 16 26s16-15 16-26C32 7 25 0 16 0z" fill="#fff"/><circle cx="16" cy="15" r="6" fill="#2f3865"/></svg>
    <div><div class="label">Our Address</div>48 Harlow Avenue Suite 5 Austin 78701 TX</div>
  </div>
  <div class="info-item abs" style="top:2632px">
    <svg width="34" height="34" viewBox="0 0 34 34"><path d="M8 2l6 8-4 4c2 5 5 8 10 10l4-4 8 6-4 6C14 32 2 20 2 6z" fill="#fff"/><path d="M20 4a12 12 0 0 1 10 10M20 10a6 6 0 0 1 4 4" stroke="#fff" stroke-width="2" fill="none"/></svg>
    <div><div class="label">Phone Number</div>(512) 555 0187</div>
  </div>
  <div class="info-item abs" style="top:2717px">
    <svg width="38" height="26" viewBox="0 0 38 26"><rect width="38" height="26" fill="#fff"/><path d="M0 0l19 14L38 0" stroke="#2f3865" stroke-width="2.5" fill="none"/></svg>
    <div><div class="label">Email address</div>info@crestlineadvisory.example</div>
  </div>
  <div class="social abs"><span></span><span></span><span></span><span></span></div>

  <div class="field abs" style="top:2538px;height:46px;padding-top:13px">Name</div>
  <div class="field abs" style="top:2596px;height:46px;padding-top:13px">Email address</div>
  <div class="field abs" style="top:2654px;height:46px;padding-top:13px">Phone Number</div>
  <div class="field abs" style="top:2712px;height:90px;padding-top:14px">Messsage</div>
  <div class="submit btn-red abs">SUBMIT</div>

  <footer class="site-footer">
    <div class="brand abs"><span class="brand-mark"></span><span>CRESTLINE<br>ADVISORY</span></div>
    <nav class="footer-nav abs"><span>HOME</span><span>ABOUT COMPANY</span><span>THE TEAM</span><span>WHAT WE DO</span><span>CONTACT US</span></nav>
    <div class="copyright abs">© 2020 Company Name | All Rights Reserved</div>
  </footer>

</div>
</body>
</html>
```